Business Card for a Dental Office

The design should communicate integrity, quality and reliability. We also want the card look elegant, simple, but still stand out, different from the traditional-dental-office business card.

Industry/Entity Type

Business

```html
<!DOCTYPE html>
<html lang="en">
<head>
<meta charset="utf-8">
<title>Harlow Dental Centre – Business Card</title>
<link href="https://fonts.googleapis.com/css2?family=Open+Sans:wght@400;600&display=swap" rel="stylesheet">
<style>
  :root {
    --backdrop: #5a3f2c;
    --card-white: #ffffff;
    --card-black: #000000;
    --ink: #1a1a1a;
    --gold: #c9b21a;
    --gold-light: #f2e521;
    --gold-dark: #8a7410;
  }
  * { margin: 0; padding: 0; box-sizing: border-box; }
  html, body { width: 1200px; height: 1000px; overflow: hidden; }
  body { background: var(--backdrop); position: relative; font-family: "Open Sans", Arial, sans-serif; color: var(--ink); }

  .card { position: absolute; left: 265px; width: 666px; height: 397px; box-shadow: 0 4px 14px rgba(0,0,0,.45); overflow: hidden; }
  .card-front { top: 73px; background: var(--card-white); }
  .card-back { top: 532px; background: var(--card-black); }

  .brand { position: absolute; display: flex; align-items: center; }
  .brand-square { background: var(--gold); flex: none; }
  .brand-name { font-family: "Open Sans", Arial, sans-serif; font-weight: 600; text-transform: uppercase; line-height: 1; white-space: nowrap; }

  .card-front .brand { left: 34px; top: 50px; }
  .card-front .brand-square { width: 64px; height: 64px; margin-right: 14px; }
  .card-front .brand-name { font-size: 28px; color: var(--ink); }

  .person { position: absolute; right: 33px; top: 203px; text-align: right; }
  .person-name { font-size: 20px; font-weight: 600; }
  .person-role { font-size: 15px; margin-top: 4px; }
  .accent-tab { position: absolute; right: 0; top: 205px; width: 13px; height: 40px; background: var(--gold); }
  .rule { position: absolute; left: 33px; top: 242px; width: 521px; height: 2px; background: var(--ink); }

  .address { position: absolute; left: 33px; top: 297px; font-size: 15.5px; line-height: 24px; font-style: normal; }
  .contacts { position: absolute; right: 32px; top: 275px; list-style: none; font-size: 15.5px; line-height: 23.5px; text-align: right; }
  .contacts li { display: flex; justify-content: flex-end; align-items: center; gap: 8px; }
  .contacts svg { width: 15px; height: 12px; fill: var(--gold); flex: none; }

  .footer-band { position: absolute; left: 0; bottom: 0; width: 100%; height: 32px;
    background: linear-gradient(90deg, var(--card-black) 0 52%, var(--gold-dark) 55%, var(--gold-light) 80%, var(--gold) 100%); }
  .footer-mark { position: absolute; left: 347px; top: 6px; width: 18px; height: 18px; background: var(--card-white); }

  .card-back .brand { left: 100px; top: 160px; }
  .card-back .brand-square { width: 76px; height: 76px; margin-right: 16px; }
  .card-back .brand-name { font-size: 33px; color: var(--card-white); }
</style>
</head>
<body>
  <section class="card card-front">
    <div class="brand">
      <span class="brand-square"></span>
      <span class="brand-name">Harlow Dental Centre</span>
    </div>

    <div class="person">
      <p class="person-name">Elliot Marsh, PHA</p>
      <p class="person-role">President</p>
    </div>
    <span class="accent-tab"></span>
    <span class="rule"></span>

    <address class="address">
      Level 12, 48 Kestrel House<br>
      Newcastle, New South Wales
    </address>

    <ul class="contacts">
      <li>+ 000 000 0000
        <svg viewBox="0 0 15 12" aria-label="Phone"><path d="M1 4c0-2 3-3 6.5-3S14 2 14 4v1h-3V3.5H4V5H1z M3 6h9l2 5H1z"/></svg>
      </li>
      <li>+ 000 000 0000
        <svg viewBox="0 0 15 12" aria-label="Fax"><path d="M4 0h7v3H4z M1 4h13v5h-2V7H3v2H1z M4 8h7v4H4z"/></svg>
      </li>
      <li>info@harlowdentalcare.com
        <svg viewBox="0 0 15 12" aria-label="Email"><path d="M0 1h15v1L7.5 7 0 2z M0 3.5l7.5 5 7.5-5V11H0z"/></svg>
      </li>
    </ul>

    <div class="footer-band"><span class="footer-mark"></span></div>
  </section>

  <section class="card card-back">
    <div class="brand">
      <span class="brand-square"></span>
      <span class="brand-name">Harlow Dental Centre</span>
    </div>
  </section>
</body>
</html>
```